American cannabis tech company business card design

Pavrel.com is seeking a modern, professional, and brand-aligned business card that represents our company and its core values: Mission, Story, Values, and Impact. As an innovative cannabis company, we want a business card that is not only visually appealing but also serves as a representation of who we are and what we stand for.

Project Scope: Design a double-sided business card that integrates our brand identity and core values. Incorporate our key brand elements, ensuring a sleek and contemporary aesthetic. Visually reflect our core values (Mission, Story, Values, Impact) in a way that is engaging yet professional.

Target Market(s)

Vendors, third parties,

Contact Information for Business Card

Contact details (name, title, email, phone, website, etc.)

Font styles to use
Other font styles liked:
• Caslon, Centra

Colors

Designer to choose colors to be used in the design.

Requirements
Must have
• Pavrel.com logo and branding A creative yet clean way to integrate our core values (Mission, Story, Values, Impact) Modern typography and a well-structured layout
Nice to have
• forest green, grey, white, black
Should not have
• references to marijuana, leafs, plants, or related product

```html
<!DOCTYPE html>
<html lang="en">
<head>
<meta charset="utf-8">
<title>Pavrel.com Business Card</title>
<link rel="stylesheet" href="https://fonts.googleapis.com/css2?family=Playfair+Display:wght@700&family=Montserrat:wght@400;500&display=swap">
<style>
  :root {
    --forest: #1c3320;
    --paper: #ffffff;
    --backdrop: #2e2e2e;
    --ink: #1c3320;
  }
  * { margin: 0; padding: 0; box-sizing: border-box; }
  html, body { width: 1200px; height: 875px; overflow: hidden; }
  body {
    background: var(--backdrop);
    display: flex;
    flex-direction: column;
    align-items: center;
    justify-content: center;
    gap: 40px;
  }
  .card {
    position: relative;
    width: 640px;
    height: 366px;
    background: var(--paper);
    border-radius: 18px;
    overflow: hidden;
  }
  .wordmark {
    font-family: "Playfair Display", Georgia, serif;
    font-weight: 700;
    color: var(--forest);
    letter-spacing: 2px;
    line-height: 1;
  }
  .card-front { display: flex; align-items: center; justify-content: center; }
  .card-front .wordmark { font-size: 112px; }

  .card-back .wordmark {
    position: absolute;
    left: 46px;
    top: 136px;
    font-size: 58px;
  }
  .divider {
    position: absolute;
    left: 330px;
    top: 90px;
    width: 1.5px;
    height: 135px;
    background: var(--forest);
  }
  .contact-block {
    position: absolute;
    left: 352px;
    top: 86px;
    color: var(--ink);
  }
  .person-name {
    font-family: "Playfair Display", Georgia, serif;
    font-weight: 700;
    font-size: 22px;
  }
  .person-title {
    font-family: "Playfair Display", Georgia, serif;
    font-weight: 700;
    font-size: 12px;
    margin: 2px 0 12px 6px;
  }
  .contact-list { list-style: none; }
  .contact-list li {
    display: flex;
    align-items: center;
    gap: 9px;
    font-family: "Montserrat", Arial, sans-serif;
    font-size: 15px;
    margin-bottom: 6px;
  }
  .contact-list svg { width: 13px; height: 13px; flex: none; }
  .address-band {
    position: absolute;
    left: 0;
    right: 0;
    top: 276px;
    height: 50px;
    background: var(--forest);
    color: var(--paper);
    font-family: "Montserrat", Arial, sans-serif;
    font-size: 15px;
    display: flex;
    align-items: center;
    justify-content: center;
  }
</style>
</head>
<body>
  <section class="card card-front">
    <div class="wordmark">PAVREL</div>
  </section>

  <section class="card card-back">
    <div class="wordmark">PAVREL</div>
    <div class="divider"></div>
    <div class="contact-block">
      <div class="person-name">Daniel Hart</div>
      <div class="person-title">Owner</div>
      <ul class="contact-list">
        <li>
          <svg viewBox="0 0 24 24" aria-hidden="true"><path fill="var(--forest)" d="M6.6 10.8a15.1 15.1 0 0 0 6.6 6.6l2.2-2.2a1 1 0 0 1 1-.25 11.4 11.4 0 0 0 3.6.57 1 1 0 0 1 1 1V20a1 1 0 0 1-1 1A17 17 0 0 1 3 4a1 1 0 0 1 1-1h3.5a1 1 0 0 1 1 1c0 1.25.2 2.45.57 3.6a1 1 0 0 1-.25 1z"/></svg>
          555-014-0192
        </li>
        <li>
          <svg viewBox="0 0 24 24" aria-hidden="true"><path fill="var(--forest)" d="M2 5h20v14H2zm2 2v.5l8 5 8-5V7z"/></svg>
          info@pavrel.com
        </li>
        <li>
          <svg viewBox="0 0 24 24" aria-hidden="true"><circle cx="12" cy="12" r="9" fill="none" stroke="var(--forest)" stroke-width="2.4"/><path d="M3 12h18M12 3c3 3 3 15 0 18M12 3c-3 3-3 15 0 18" fill="none" stroke="var(--forest)" stroke-width="1.8"/></svg>
          www.pavrel.com
        </li>
      </ul>
    </div>
    <div class="address-band">415 Linden Ave, #112 Brookfield, OH 43210</div>
  </section>
</body>
</html>
```